Classy, Elegant, Simple Business Card Design

Looking to have a classy, simple, and elegant design. Want a top notch designed business card. I really like the look of the new torvane credit card. I also like the design I attached. I am trying to reach 21-29 year old females for booking us for there wedding or event. We offer Disc Jockey Service, Photo Booth Rentals, and Uplighting .

Target Market(s)

21-28 year old females

Contact Information for Business Card

Has to have logo, website, email, and phone number

Font styles to use
Other font styles liked:
• open to font choice, modern, clean
Designer to choose
33a6d7
0791cd
0555a3
ffffff

Requirements
Must have
• Has to have logo, website, email, and phone number
Nice to have
• I really like the design of the new torvane credit card. I also included my logo and some designs I like
Should not have
• clutter or too much info

```html
<!DOCTYPE html>
<html lang="en">
<head>
<meta charset="utf-8">
<title>Echoline Event Group – Business Card</title>
<link href="https://fonts.googleapis.com/css2?family=Jost:wght@400;500;600&display=swap" rel="stylesheet">
<style>
  :root {
    --backdrop: #25282e;
    --card-navy: #123a6b;
    --card-deep: #0b2b55;
    --pattern-light: #21599a;
    --pattern-mid: #184a85;
    --brand-sky: #33a6d7;
    --brand-blue: #0791cd;
    --brand-royal: #0555a3;
    --white: #ffffff;
  }
  * { margin: 0; padding: 0; box-sizing: border-box; }
  html, body {
    width: 1200px; height: 900px; overflow: hidden;
    background: var(--backdrop);
    font-family: "Jost", sans-serif;
  }
  .canvas {
    width: 1200px; height: 900px;
    display: flex; flex-direction: column;
    align-items: center; justify-content: center; gap: 44px;
  }
  .card {
    position: relative;
    width: 640px; height: 366px;
    background: var(--card-navy);
    border-radius: 6px;
    overflow: hidden;
    box-shadow: 0 14px 30px rgba(0,0,0,0.45);
  }
  .card-pattern {
    position: absolute;
    border-radius: 50%;
  }
  .card--contact .card-pattern {
    width: 600px; height: 600px; left: -300px; top: -330px;
    background: radial-gradient(circle, var(--card-navy) 0 32%, var(--pattern-mid) 40%, var(--pattern-light) 50%, var(--pattern-mid) 60%, var(--card-navy) 70%);
  }
  .card--brand .card-pattern {
    width: 640px; height: 640px; right: -340px; top: -140px;
    background: radial-gradient(circle, var(--card-navy) 0 30%, var(--pattern-mid) 38%, var(--pattern-light) 48%, var(--pattern-mid) 58%, var(--card-navy) 70%);
  }
  .holder-name {
    position: absolute; left: 44px; top: 60px;
    color: var(--white);
    font-weight: 600; font-size: 26px; letter-spacing: 1px;
    text-transform: uppercase;
  }
  .brand-mark {
    display: flex; align-items: center; gap: 12px;
    color: var(--brand-sky);
    font-weight: 500; font-size: 30px; letter-spacing: 3px;
    text-transform: uppercase;
    white-space: nowrap;
  }
  .brand-dot {
    width: 18px; height: 18px; border-radius: 50%;
    background: var(--brand-sky);
    flex: none;
  }
  .card--contact .brand-mark {
    position: absolute; left: 250px; top: 140px;
    font-size: 20px; letter-spacing: 2px; gap: 10px;
  }
  .card--contact .brand-dot { width: 14px; height: 14px; }
  .card--brand .brand-mark {
    position: absolute; left: 0; right: 0; top: 162px;
    justify-content: center;
  }
  .contact-list {
    position: absolute; left: 252px; top: 196px;
    list-style: none;
    color: var(--white);
    font-size: 19px; line-height: 34px;
  }
  .contact-list li { display: flex; align-items: center; gap: 12px; white-space: nowrap; }
  .contact-icon { width: 16px; height: 16px; flex: none; }
</style>
</head>
<body>
<main class="canvas">
  <section class="card card--contact">
    <div class="card-pattern" role="img" aria-label="Faint radial mosaic of equalizer squares"></div>
    <h1 class="holder-name">Miles Danford</h1>
    <div class="brand-mark"><span class="brand-dot"></span>Echoline Event Group</div>
    <ul class="contact-list">
      <li>
        <svg class="contact-icon" viewBox="0 0 16 16"><path fill="#33a6d7" d="M3.5 1.5l2.5 3-1.5 1.5c.8 2 2.5 3.7 4.5 4.5l1.5-1.5 3 2.5-1.8 2.3C6.6 13.3 2.7 9.4 1.2 3.3z"/></svg>
        0000 412 587
      </li>
      <li>
        <svg class="contact-icon" viewBox="0 0 16 16"><rect x="1" y="3" width="14" height="10" fill="#33a6d7"/><path d="M1 3l7 6 7-6" fill="none" stroke="#123a6b" stroke-width="1.4"/></svg>
        hello@echolineevents.com
      </li>
      <li>
        <svg class="contact-icon" viewBox="0 0 16 16"><g fill="none" stroke="#33a6d7" stroke-width="1.4"><circle cx="8" cy="8" r="6.5"/><ellipse cx="8" cy="8" rx="3" ry="6.5"/><path d="M1.5 8h13"/></g></svg>
        www.echolineevents.com
      </li>
    </ul>
  </section>

  <section class="card card--brand">
    <div class="card-pattern" role="img" aria-label="Faint radial mosaic of equalizer squares"></div>
    <div class="brand-mark"><span class="brand-dot"></span>Echoline Event Group</div>
  </section>
</main>
</body>
</html>
```